Zielgruppe
Immobilienmakler
Aufgabenstellung
Top moderne hochwertige Visitenkate, wir hätten gerne eine sehr hochwertig moderne Visitenkarte mit Bild vom Mitarbeiter... Anbei habe ich die alte Visitenkarte die ich sehr kindlich finde... Es sollte jetzt sehr exklusive aussehen. Alle Daten können von der alten Visitenkarte übernommen werden.. danke

```html
<!DOCTYPE html>
<html lang="de">
<head>
<meta charset="utf-8">
<title>Velta Agentur – Visitenkarte</title>
<link rel="stylesheet" href="https://fonts.googleapis.com/css2?family=Ubuntu:wght@400;500;700&display=swap">
<style>
  :root {
    --green: #1b8a42;
    --ink: #2b2b2b;
    --paper: #ffffff;
    --stage: #e3e3e1;
    --photo-light: #e9ecef;
    --photo-dark: #9aa3ad;
  }
  * { margin: 0; padding: 0; box-sizing: border-box; }
  html, body { width: 1200px; height: 764px; overflow: hidden; }
  body {
    background: var(--stage);
    font-family: "Ubuntu", sans-serif;
    color: var(--ink);
    position: relative;
  }
  .card {
    position: absolute;
    top: 155px;
    width: 315px;
    height: 487px;
    background: var(--paper);
    box-shadow: 0 4px 14px rgba(0,0,0,0.18);
  }
  .card--front { left: 252px; }
  .card--back { left: 632px; }

  .brand {
    position: absolute;
    left: 40px;
    display: flex;
    align-items: center;
    gap: 6px;
  }
  .brand__dot {
    width: 12px; height: 12px;
    border-radius: 50%;
    background: var(--green);
  }
  .brand__name {
    font-weight: 700;
    font-size: 33px;
    letter-spacing: -0.5px;
    color: var(--ink);
    white-space: nowrap;
  }
  .tagline {
    position: absolute;
    right: 41px;
    font-size: 10.5px;
    letter-spacing: 0.8px;
    text-transform: uppercase;
    color: var(--ink);
  }
  .card--front .brand { top: 185px; }
  .card--front .tagline { top: 228px; }
  .card--back .brand { top: 50px; }
  .card--back .tagline { top: 91px; }

  .address {
    position: absolute;
    left: 40px; top: 119px;
    font-size: 14px;
  }
  .contact {
    position: absolute;
    left: 40px; top: 147px;
    font-size: 14px;
    line-height: 17.5px;
    border-collapse: collapse;
  }
  .contact th { font-weight: 400; text-align: left; width: 54px; }
  .contact td { padding: 0; }

  .portrait {
    position: absolute;
    left: 139px; top: 226px;
    width: 114px; height: 114px;
    border-radius: 50%;
    background: radial-gradient(circle at 50% 40%, var(--photo-light) 0%, var(--photo-light) 45%, var(--photo-dark) 100%);
    box-shadow: 0 1px 4px rgba(0,0,0,0.2);
  }
  .portrait-pointer {
    position: absolute;
    left: 160px; top: 329px;
  }

  .person {
    position: absolute;
    left: 41px; top: 359px;
    font-size: 14px;
    line-height: 17.5px;
  }
  .person__name {
    color: var(--green);
    font-size: 16.5px;
    line-height: 20px;
  }

  .web-band {
    position: absolute;
    left: 0; bottom: 0;
    width: 100%; height: 39px;
    background: var(--green);
  }
  .web-band__url {
    position: absolute;
    right: 37px; top: 10px;
    font-size: 14px;
    color: var(--paper);
  }
</style>
</head>
<body>

  <section class="card card--front">
    <div class="brand">
      <span class="brand__name">Velta Agentur</span>
      <span class="brand__dot"></span>
    </div>
    <p class="tagline">Der Immobilienmakler</p>
    <div class="web-band"><span class="web-band__url">www.velta-agentur.de</span></div>
  </section>

  <section class="card card--back">
    <div class="brand">
      <span class="brand__name">Velta Agentur</span>
      <span class="brand__dot"></span>
    </div>
    <p class="tagline">Der Immobilienmakler</p>

    <p class="address">Am Anger 14 · 6850 Dornbirn</p>
    <table class="contact">
      <tr><th>Telefon</th><td>+43 5572 41 208 30</td></tr>
      <tr><th>Mobil</th><td>+43 664 2870 415</td></tr>
      <tr><th>E-Mail</th><td>lorenz@velta-agentur.com</td></tr>
    </table>

    <div class="portrait" role="img" aria-label="Porträtfoto des Mitarbeiters Lorenz Haller"></div>
    <svg class="portrait-pointer" width="34" height="32" viewBox="0 0 34 32" aria-hidden="true">
      <polygon points="4,2 31,8 8,31" fill="#1e1e1e"/>
    </svg>

    <div class="person">
      <p class="person__name">Lorenz Haller</p>
      <p>Dipl. Immobilienmanager</p>
      <p>Geschäftsführer</p>
    </div>

    <div class="web-band"><span class="web-band__url">www.velta-agentur.de</span></div>
  </section>

</body>
</html>
```